Gymnastics and fitness web design

Valdrey Gymnastics and fitness centre is opening a new branch in the United States.
Target Audience:
22 to 40 year old people who are not satisfied with their current body figure, shape and size.
and
Our programs
VoltaRig, Sports performance and personal training
DESIGN STYLE:
We want the site to be trendy, edgy and cool. The colors we prefer are blue, black and silver. Th idea is people should get motivated by seeing our website. We don't like adding many text in the design, images oriented design is what we are after.
Contents should be added-
Slider
who we are?
section for our programs
Why us?
Video showing some tutorials
Articles
contact us form with map, Address, Phone number, timings, and social media buttons.

```html
<!DOCTYPE html>
<html lang="en">
<head>
<meta charset="utf-8">
<title>Valdrey Gymnastics &amp; Fitness Centre</title>
<link rel="stylesheet" href="https://fonts.googleapis.com/css2?family=Russo+One&family=Montserrat:wght@400;500;600&display=swap">
<style>
:root{
  --blue:#1530e6;
  --blue-btn:#2238d8;
  --black:#000;
  --white:#fff;
  --bar:#e4e4e4;
  --strip:#d6d6d6;
  --ink:#222;
  --muted:#444;
}
*{margin:0;padding:0;box-sizing:border-box}
html,body{width:1200px;height:1200px;overflow:hidden;background:var(--black)}
body{position:relative;font-family:"Montserrat",sans-serif;color:var(--ink)}
.display{font-family:"Russo One",sans-serif;letter-spacing:1.5px}

.top-bar{position:absolute;left:0;top:0;width:1200px;height:35px;background:var(--bar);font-size:7px;line-height:8px;color:var(--muted)}
.top-bar .info{position:absolute;top:10px}
.top-bar .sep{position:absolute;top:7px;width:1px;height:21px;background:#bbb}
.appointment{position:absolute;left:794px;top:5px;width:153px;height:24px;background:var(--blue-btn);color:var(--white);font-size:9.5px;font-weight:600;display:flex;align-items:center;justify-content:center;border-radius:2px}

.main-nav{position:absolute;left:0;top:35px;width:1200px;height:73px;background:var(--black)}
.brand{position:absolute;left:250px;top:18px;color:var(--blue)}
.brand-name{font-family:"Russo One",sans-serif;font-size:29px;line-height:28px;letter-spacing:1px}
.brand-tag{font-size:8px;color:var(--white);letter-spacing:1px;margin-top:2px;font-weight:500}
.menu{position:absolute;top:23px;left:601px;display:flex;font-size:11.5px;font-weight:500;color:var(--white)}
.menu span{height:25px;display:flex;align-items:center;justify-content:center}
.menu .active{width:67px;border:1px solid var(--blue);border-radius:2px}

.hero{position:absolute;left:0;top:108px;width:1200px;height:412px;overflow:hidden}
.hero-photo{position:absolute;inset:0;background:
  radial-gradient(ellipse 260px 300px at 960px 210px,#5a5c60 0%,#5a5c6000 100%),
  radial-gradient(ellipse 340px 420px at 1200px 230px,#1c1c1c 0%,#1c1c1c00 100%),
  radial-gradient(ellipse 520px 300px at 520px 190px,#dfe2e8 0%,#dfe2e800 100%),
  linear-gradient(90deg,#8d8f93 0%,#b5b8be 18%,#c9ccd2 40%,#c3c6cc 62%,#8a8b8e 80%,#3c3c3c 100%)}
.hero-photo::before{content:"";position:absolute;left:0;top:0;right:0;height:90px;background:linear-gradient(#00000040,#00000000)}
.hero-photo::after{content:"";position:absolute;left:0;right:0;bottom:0;height:64px;background:linear-gradient(#4a4a4a00,#303030 40%,#1e1e1e)}
.hero-title{position:absolute;left:250px;top:64px;font-size:50px;line-height:52px;color:var(--blue);letter-spacing:3px}
.hero-text{position:absolute;left:251px;top:120px;width:260px;font-size:12px;line-height:15.5px;color:#1a1a1a;font-weight:500}
.btn{display:flex;align-items:center;justify-content:center;color:var(--white);font-weight:600;background:linear-gradient(#2f48ec,#1428c8);border-radius:2px}
.hero-btn{position:absolute;left:250px;top:194px;width:150px;height:33px;font-size:10.5px}

.promise{position:absolute;left:0;top:520px;width:1200px;height:86px;background:var(--strip)}
.promise-title{position:absolute;left:251px;top:28px;font-size:12.5px;line-height:15px;color:#111;letter-spacing:.5px}
.promise-rule{position:absolute;left:385px;top:28px;width:2px;height:30px;background:var(--blue)}
.promise-text{position:absolute;left:413px;top:29px;width:520px;font-size:10.8px;line-height:14.5px;color:#333}

.programs-head{position:absolute;left:0;top:606px;width:1200px;height:178px;text-align:center;color:var(--white)}
.programs-head h2{font-weight:400;font-size:25px;margin-top:58px;letter-spacing:3px}
.programs-head p{font-size:11.5px;font-weight:500;margin-top:12px}

.program{position:absolute;top:784px;height:356px;display:flex;align-items:center;justify-content:center;text-align:center;overflow:hidden}
.program h3{position:relative;font-weight:400;font-size:24px;line-height:30px;color:#e8eaff;letter-spacing:2px}
.p1{left:0;width:292px;background:
  radial-gradient(ellipse 150px 170px at 120px 170px,#2c4cf2 0%,#2c4cf200 100%),
  radial-gradient(ellipse 120px 80px at 140px 40px,#3a58f4 0%,#3a58f400 100%),
  linear-gradient(100deg,#1637dc,#0a29c9 70%,#0722b4)}
.p2{left:292px;width:305px;background:
  radial-gradient(ellipse 150px 190px at 190px 200px,#3150f2 0%,#3150f200 100%),
  radial-gradient(ellipse 90px 70px at 220px 60px,#2646ee 0%,#2646ee00 100%),
  linear-gradient(110deg,#0925c2,#0d2ed4 55%,#0a28c8)}
.p3{left:597px;width:304px;background:
  radial-gradient(ellipse 140px 200px at 150px 150px,#d6d6d6 0%,#d6d6d600 100%),
  linear-gradient(90deg,#b9b9b9,#cdcdcd 50%,#b3b3b3)}
.p3::after{content:"";position:absolute;left:0;right:0;bottom:0;height:50px;background:linear-gradient(#a0a0a000,#9a9a9a)}
.p4{left:901px;width:299px;background:
  radial-gradient(ellipse 170px 200px at 150px 200px,#4560f7 0%,#4560f700 100%),
  radial-gradient(ellipse 100px 80px at 140px 50px,#1f3be0 0%,#1f3be000 100%),
  linear-gradient(100deg,#2a48f0,#3450f4 50%,#2340e6)}
.p3 .frame{position:absolute;left:10px;top:8px;right:10px;bottom:9px;border:1.5px solid #222;z-index:1}
.p3 .content{position:relative;width:240px;z-index:2;margin-top:-14px}
.p3 h3{color:var(--blue);margin-bottom:20px}
.p3 p{font-size:10.5px;line-height:14.5px;color:#2a2a2a;margin-bottom:30px}
.p3 .btn{width:150px;height:33px;margin:0 auto;font-size:10.5px}
</style>
</head>
<body>

<header class="top-bar">
  <div class="info" style="left:251px">Monday - Friday 13:30 - 17:30<br>Saturday and Sunday closed</div>
  <div class="sep" style="left:378px"></div>
  <div class="info" style="left:401px">0555 310 7284<br>info@valdreygfc.com</div>
  <div class="sep" style="left:507px"></div>
  <div class="info" style="left:533px">Lorem ipsum dolor sit amet, consectetur adipiscing<br>elit. Sed semper massa sit amet</div>
  <div class="appointment">MAKE AN APPOINTMENT</div>
</header>

<nav class="main-nav">
  <div class="brand">
    <div class="brand-name">VALDREY</div>
    <div class="brand-tag">GYMNASTICS &amp; FITNESS CENTRE</div>
  </div>
  <div class="menu">
    <span class="active">Home</span>
    <span style="width:85px">About</span>
    <span style="width:80px">Programs</span>
    <span style="width:75px">Blog</span>
    <span style="width:73px">Contact</span>
  </div>
</nav>

<section class="hero">
  <div class="hero-photo" role="img" aria-label="Athlete training with battle ropes in front of a white brick wall"></div>
  <h1 class="hero-title display">VALDREY</h1>
  <p class="hero-text">Lorem ipsum dolor sit amet, consectetur adipiscing elit. Sed semper massa sit amet urna bibendum dapibus. Nunc eleifend</p>
  <div class="btn hero-btn">SEE OUR SERVICES</div>
</section>

<section class="promise">
  <div class="promise-title display">COMPLETE<br>PEACE OF MIND</div>
  <div class="promise-rule"></div>
  <p class="promise-text">Lorem ipsum dolor sit amet, consectetur adipiscing elit. Sed semper massa sit amet Lorem ipsum dolor sit amet, consectetur adipiscing elit. Sed semper massa sit amet</p>
</section>

<section class="programs-head">
  <h2 class="display">OUR PROGRAMS</h2>
  <p>Lorem ipsum dolor sit amet, consectetur adipiscing elit. Sed semper massa sit amet</p>
</section>

<article class="program p1" role="img" aria-label="Blue-toned photo of a woman's back in a sports top">
  <h3 class="display">PROGRAM<br>ONE</h3>
</article>
<article class="program p2" role="img" aria-label="Blue-toned photo of a man lifting a dumbbell">
  <h3 class="display">PROGRAM<br>TWO</h3>
</article>
<article class="program p3" role="img" aria-label="Grey-toned photo of an athlete with battle ropes">
  <div class="frame"></div>
  <div class="content">
    <h3 class="display">PROGRAM<br>THREE</h3>
    <p>Lorem ipsum dolor sit amet, consectetur adipiscing elit. Sed semper massa sit amet Lorem ipsum dolor sit amet, consectetur</p>
    <div class="btn">READ MORE</div>
  </div>
</article>
<article class="program p4" role="img" aria-label="Blue-toned photo of an athlete holding a ball">
  <h3 class="display">PROGRAM<br>FOUR</h3>
</article>

</body>
</html>
```